The Vellmark Company Sweet Packaging Design

The Vellmark Goods Company is looking for a logo and label design for an upcoming line of honey based health and beauty products that are sourced from the Polynesian Islands (Hawaii, New Zealand, Fiji etc.).The brand will be premium price positioned and the design and packaging should exude class and quality.The design should be flexible enough to add products from future locations.We would like to see the design across three different product forms:1. Glass Honey Jar (main product)2. Hand cream / lotion (pump bottle, or lotion tube)3. Small box (e.g. throat lozenges / gum packet etc.)The Polynesia Islands are unique and exotic locations; the design/packaging should reflect this but should not be overly complicated. Each individual island has their own distinct culture and history but they have many commonalities which fall under "Polynesian Culture". The Vellmark Goods Company is an umbrella brand that should be able to support a growing number of products.Possible designs may (but are not required to) incorporate local flowers (Hawaii / Hibiscus flower, New Zealand / Manuka Flower etc.) into the design, Islands, and boutique feel (elegant classy looking)Please feel free to ask more questions for further guidance but we really want to see where the creative process can take us outside of what we have already considered internally.
Updates

We needed to modify our idea slightly because of competition.

We needed extend to get a few more ideas. We did not want to copy our competition and needed to add a part to our design that we did not include before.

Target Market(s)

Health conscious people. Honey lovers.

Font styles to use
Serif
Sans Serif
Decorative

Colors

Designer to choose colors to be used in the design.

Requirements
Must have
• a little tribal look. because its 100% polynesian Honey.. it would be nice to have the fee of that in the design..

```html
<!DOCTYPE html>
<html lang="en">
<head>
<meta charset="utf-8">
<title>Packaging Series – Proposition 2</title>
<link rel="stylesheet" href="https://fonts.googleapis.com/css2?family=Montserrat:wght@400;500&display=swap">
<style>
  :root {
    --green: #3bb54a;
    --yellow: #f8dc2f;
    --ink: #111111;
    --frame: #555555;
    --paper: #ffffff;
  }
  * { box-sizing: border-box; margin: 0; padding: 0; }
  html, body { width: 1200px; height: 1200px; overflow: hidden; background: var(--paper); }
  body { position: relative; font-family: "Montserrat", sans-serif; color: var(--ink); }

  .heading { position: absolute; left: 58px; color: var(--green); font-weight: 400; letter-spacing: 4px; font-size: 48px; line-height: 1; }
  .heading--series { top: 55px; }
  .heading--proposition { top: 114px; letter-spacing: 3px; }
  .intro { position: absolute; left: 58px; top: 188px; color: var(--green); font-size: 21px; line-height: 30px; letter-spacing: 2.2px; }

  .label { position: absolute; border: 1px solid var(--frame); background: var(--paper); }
  .label--cream { left: 62px; top: 317px; width: 321px; height: 680px; }
  .label--box { left: 407px; top: 317px; width: 628px; height: 382px; }
  .label--jar { left: 408px; top: 722px; width: 741px; height: 425px; }

  .seal { position: absolute; }
  .brand-name { position: absolute; text-align: center; text-transform: uppercase; font-weight: 500; letter-spacing: 2.4px; white-space: nowrap; }

  .info { position: absolute; border: 2px solid var(--yellow); }
  .info__row { border-top: 2px solid var(--yellow); display: flex; align-items: center; padding-left: 20px; font-size: 15px; line-height: 29px; letter-spacing: 0.3px; }
  .info__title { padding: 12px 0 0 20px; font-size: 23px; line-height: 35.5px; letter-spacing: 0.6px; }
  .info__row:first-child { border-top: 0; }
</style>
</head>
<body>
  <h1 class="heading heading--series">PACKAGING SERIES</h1>
  <h2 class="heading heading--proposition">Proposition 2</h2>
  <p class="intro">Minimalistic labels using a touch of yellow on white back-<br>ground. Logo will be replaced with the version of your choice.</p>

  <!-- Hand cream label -->
  <section class="label label--cream">
    <svg class="seal" style="left:97px;top:38px" width="128" height="128" viewBox="0 0 128 128" aria-hidden="true">
      <circle cx="64" cy="64" r="60" fill="none" stroke="var(--yellow)" stroke-width="4"/>
    </svg>
    <div class="brand-name" style="left:0;right:0;top:181px;font-size:21px;line-height:30px">The Vellmark<br>Goods Company</div>
    <div class="info" style="left:52px;top:298px;width:217px;height:334px">
      <div class="info__title" style="height:141px">Manuka Honey<br>Moisturizing<br>Hand Cream</div>
      <div class="info__row" style="height:90px">Made from 100%<br>Polynesian Honey.</div>
      <div class="info__row" style="height:55px">For sensitive skin.</div>
      <div class="info__row" style="height:44px">125 ml | 4.25 fl oz.</div>
    </div>
  </section>

  <!-- Lozenge box label -->
  <section class="label label--box">
    <svg class="seal" style="left:95px;top:94px" width="128" height="128" viewBox="0 0 128 128" aria-hidden="true">
      <circle cx="64" cy="64" r="60" fill="none" stroke="var(--yellow)" stroke-width="4"/>
    </svg>
    <div class="brand-name" style="left:39px;width:240px;top:236px;font-size:21px;line-height:30px">The Vellmark<br>Goods Company</div>
    <div class="info" style="left:332px;top:93px;width:242px;height:194px">
      <div class="info__title" style="height:127px">Hibiscus Honey<br>Antibacterial<br>Throat Lozenges</div>
      <div class="info__row" style="height:63px">16 Soothing Lozenges</div>
    </div>
  </section>

  <!-- Honey jar label -->
  <section class="label label--jar">
    <svg class="seal" style="left:316px;top:17px" width="104" height="104" viewBox="0 0 104 104" aria-hidden="true">
      <circle cx="52" cy="52" r="48" fill="none" stroke="var(--yellow)" stroke-width="3.5"/>
    </svg>
    <div class="brand-name" style="left:0;right:0;top:131px;font-size:17px;line-height:24px;letter-spacing:2px">The Vellmark<br>Goods Company</div>
    <div class="info" style="left:283px;top:200px;width:175px;height:207px">
      <div class="info__title" style="height:123px;padding-left:12px">Manuka<br>Blossom<br>Honey</div>
      <div class="info__row" style="height:41px;padding-left:12px">New Zealand</div>
      <div class="info__row" style="height:39px;padding-left:12px">250 ml | 8.45 fl oz.</div>
    </div>
  </section>
</body>
</html>
```